Automotive Accessories Business Card

Design a business template that match our new logo design and our industry.

https://www.qelmotorgear.com/

Target Market(s)

Aftermarket auto parts and accessories

Industry/Entity Type

automotive

Contact Information for Business Card

company logo

Font styles to use
Serif
Sans Serif

Colors
EB3D1F
EC4F4E
F09395
F8D3D4
FCEDEE

```html
<!DOCTYPE html>
<html lang="en">
<head>
<meta charset="utf-8">
<title>QEL Motor Gear – Business Card</title>
<link rel="stylesheet" href="https://fonts.googleapis.com/css2?family=Montserrat:wght@400;700&display=swap">
<style>
  :root {
    --backdrop: #979797;
    --card: #414042;
    --red: #d71f26;
    --white: #ffffff;
    --text-light: #f2f2f2;
  }
  * { margin: 0; padding: 0; box-sizing: border-box; }
  html, body { width: 1200px; height: 1059px; overflow: hidden; }
  body {
    background: var(--backdrop);
    font-family: "Montserrat", sans-serif;
    position: relative;
  }
  .card {
    position: absolute;
    left: 255px;
    width: 690px;
    height: 392px;
    background: var(--card);
    overflow: hidden;
  }
  .card--front { top: 89px; }
  .card--back { top: 569px; }

  .brand {
    position: absolute;
    display: flex;
    align-items: center;
    color: var(--white);
    font-weight: 700;
    white-space: nowrap;
  }
  .brand__mark { background: var(--red); flex: none; }
  .card--front .brand { left: 46px; top: 178px; font-size: 27px; gap: 10px; }
  .card--front .brand__mark { width: 22px; height: 22px; }
  .card--back .brand { left: 0; right: 0; top: 170px; justify-content: center; font-size: 46px; gap: 16px; }
  .card--back .brand__mark { width: 36px; height: 36px; }

  .divider {
    position: absolute;
    left: 343px;
    top: 102px;
    width: 1px;
    height: 186px;
    background: var(--red);
  }
  .contact {
    position: absolute;
    left: 372px;
    top: 98px;
    color: var(--text-light);
    font-size: 17px;
    line-height: 1.2;
  }
  .contact__name {
    color: var(--red);
    font-weight: 700;
    font-size: 26px;
    letter-spacing: 0.5px;
    line-height: 1;
  }
  .contact__title { margin-top: 4px; }
  .contact__address { margin-top: 14px; }
  .contact__list { list-style: none; margin-top: 14px; }
  .contact__list li { display: flex; align-items: center; gap: 6px; height: 26.5px; }
  .contact__icon { width: 12px; height: 12px; flex: none; }

  .finish-band {
    position: absolute;
    left: 0;
    bottom: 0;
    width: 100%;
    height: 14px;
    background: linear-gradient(to bottom, var(--white) 0 50%, var(--red) 50% 100%);
    opacity: 0.9;
  }
</style>
</head>
<body>
  <section class="card card--front">
    <div class="brand"><span class="brand__mark"></span>QEL MOTOR GEAR</div>
    <div class="divider"></div>
    <div class="contact">
      <p class="contact__name">DANA WHITLOCK</p>
      <p class="contact__title">CEO/Founder</p>
      <p class="contact__address">250 W. Harbor Ave. Unit B<br>Riverside, CA, 92501</p>
      <ul class="contact__list">
        <li>
          <svg class="contact__icon" viewBox="0 0 24 24" aria-hidden="true"><path fill="#d71f26" d="M6.6 10.8a15.1 15.1 0 0 0 6.6 6.6l2.2-2.2a1 1 0 0 1 1-.25 11.4 11.4 0 0 0 3.6.57 1 1 0 0 1 1 1V20a1 1 0 0 1-1 1A17 17 0 0 1 3 4a1 1 0 0 1 1-1h3.5a1 1 0 0 1 1 1c0 1.25.2 2.45.57 3.6a1 1 0 0 1-.25 1z"/></svg>
          1-866-555-0142
        </li>
        <li>
          <svg class="contact__icon" viewBox="0 0 24 24" aria-hidden="true"><rect x="2" y="5" width="20" height="14" fill="#d71f26"/><path d="M2 5l10 8 10-8" fill="none" stroke="#414042" stroke-width="2"/></svg>
          sales@qelmotorgear.com
        </li>
        <li>
          <svg class="contact__icon" viewBox="0 0 24 24" aria-hidden="true"><g fill="none" stroke="#d71f26" stroke-width="2"><circle cx="12" cy="12" r="10"/><ellipse cx="12" cy="12" rx="4" ry="10"/><path d="M2 12h20M4 7h16M4 17h16"/></g></svg>
          www.qelmotorgear.com
        </li>
      </ul>
    </div>
    <div class="finish-band" role="img" aria-label="Red and white checkered racing strip along the bottom edge"></div>
  </section>

  <section class="card card--back">
    <div class="brand"><span class="brand__mark"></span>QEL MOTOR GEAR</div>
  </section>
</body>
</html>
```